Business Cards Design for the electrical wholesaler: clean bold dynamic :)

We need a business card design that would follow our latest brand guidelines. As an electrical wholesaler we want to bring a fresh look and feel into the industry. The design should be clean bold and dynamic. It should come alive with the renewed energy of our green colour. Our grey colour should keep things balanced and complement the notion of maturity and responsibility. We employ Lato as a corporate font however are not bound by this font and we’re open to interpretation here.

Target Market(s)

Electrical contractors

Industry/Entity Type

Business

Contact Information for Business Card

Logo
Name & Surname: Halyna Dorosh
Job Title: Director of Marketing
Email: halya.dorosh@quillmail.example
Cell phone: XXX.XXX.XXXX
Address: 20517 - 87 Ave. Edmonton, AB, Canada. T6K 4N8
Business Phone: 780.555.0184
Website: www.brovix.example

Font styles to use
Other font styles liked:
• Lato

Requirements
Must have
• Logo & website
Nice to have
• Brand elements - some of them you may find in the attached Brand Guidelines (e.g. three lines on the background signifying "W")

```html
<!DOCTYPE html>
<html lang="en">
<head>
<meta charset="utf-8">
<title>Brovix Business Cards</title>
<link rel="stylesheet" href="https://fonts.googleapis.com/css2?family=Work+Sans:wght@400;500;600&display=swap">
<style>
  :root{
    --bg:#d9d6d2;
    --card:#1c1c1c;
    --card-edge:#141414;
    --green:#7ac143;
    --white:#f4f4f4;
    --grey:#cfcfcf;
  }
  *{margin:0;padding:0;box-sizing:border-box}
  html,body{width:1200px;height:715px;overflow:hidden}
  body{background:var(--bg);font-family:"Work Sans",sans-serif;position:relative}
  .card{
    position:absolute;top:209px;width:520px;height:297px;
    background:var(--card);border-radius:4px;
    box-shadow:0 6px 18px rgba(0,0,0,.25);
  }
  .card--front{left:50px;border-bottom:4px solid var(--green)}
  .card--back{left:630px}
  .brand{display:flex;align-items:center;gap:12px;color:var(--white);font-weight:600;letter-spacing:.5px}
  .brand__mark{background:var(--green);flex:none}
  .card--front .brand{position:absolute;left:50%;top:50%;transform:translate(-50%,-50%);font-size:62px}
  .card--front .brand__mark{width:44px;height:44px}
  .card--back .brand{position:absolute;left:40px;top:118px;font-size:38px;gap:9px}
  .card--back .brand__mark{width:27px;height:27px}
  .divider{position:absolute;left:258px;top:70px;width:2px;height:160px;background:var(--green)}
  .contact{position:absolute;left:282px;top:70px;color:var(--white);font-size:13px;line-height:1.5}
  .contact__name{color:var(--green);font-size:21px;font-weight:500;line-height:1.1}
  .contact__title{margin-bottom:8px}
  .contact__row{display:flex;align-items:center;gap:7px;margin-left:-17px}
  .contact__row svg{width:10px;height:10px;flex:none}
</style>
</head>
<body>
  <section class="card card--front" aria-label="Card front">
    <div class="brand"><span class="brand__mark"></span><span class="brand__name">brovix</span></div>
  </section>

  <section class="card card--back" aria-label="Card back">
    <div class="brand"><span class="brand__mark"></span><span class="brand__name">brovix</span></div>
    <div class="divider"></div>
    <div class="contact">
      <p class="contact__name">Halyna Dorosh</p>
      <p class="contact__title">Founder</p>
      <p>20517 87ave</p>
      <p>T6K4N8 Edmonton, Alberta</p>
      <p class="contact__row">
        <svg viewBox="0 0 10 10"><path d="M2 1l2 2-1 1.3c.6 1.2 1.5 2.1 2.7 2.7L7 6l2 2-1.3 1.3C4.5 9 1 5.5.7 2.3z" fill="var(--green)"/></svg>
        <span>780.555.0184</span>
      </p>
      <p class="contact__row">
        <svg viewBox="0 0 10 10"><rect x=".8" y="2" width="8.4" height="6" fill="none" stroke="var(--green)"/><path d="M.8 2L5 5.5 9.2 2" fill="none" stroke="var(--green)"/></svg>
        <span>hello@brovix.example</span>
      </p>
      <p class="contact__row">
        <svg viewBox="0 0 10 10"><circle cx="5" cy="5" r="4.2" fill="none" stroke="var(--green)"/><path d="M.8 5h8.4M5 .8c-2.4 2.4-2.4 6 0 8.4M5 .8c2.4 2.4 2.4 6 0 8.4" fill="none" stroke="var(--green)" stroke-width=".8"/></svg>
        <span>www.brovix.example</span>
      </p>
    </div>
  </section>
</body>
</html>
```